Business Card for my New Brokerage

Looking to get a business card design for my new Real Estate Brokerage.
I want it with Picture, Phone Number, Email, Website, Office Address
Name and Designation. Please add logo too.

Target Market(s)

Real Estate Investors or Home Buyers

Industry/Entity Type

Real Estate

Contact Information for Business Card

Name, Email, Phone Number, website, email, office address

Colors
EB3D1F
EC4F4E
F09395
F8D3D4
FCEDEE

Requirements
Must have
• Minimalistic, Clean, Modern, Photo
Nice to have
• White and Red Colors

```html
<!DOCTYPE html>
<html lang="en">
<head>
<meta charset="utf-8">
<title>Ember Key Realty – Business Card</title>
<link href="https://fonts.googleapis.com/css2?family=Lato:wght@400;700;900&display=swap" rel="stylesheet">
<style>
  :root {
    --stage: #0d0d0d;
    --card: #262628;
    --card-back: #2a2a2c;
    --red: #e00d0d;
    --edge: #d80a0a;
    --ink: #f2f2f2;
    --muted: #d8d8d8;
  }
  * { box-sizing: border-box; margin: 0; padding: 0; }
  html, body { width: 1200px; height: 820px; overflow: hidden; }
  body {
    background: var(--stage);
    font-family: "Lato", Arial, sans-serif;
    color: var(--ink);
    position: relative;
  }
  .card {
    position: absolute;
    width: 525px;
    height: 300px;
    border-bottom: 4px solid var(--edge);
    border-left: 3px solid var(--edge);
  }
  .card--front { left: 55px; top: 400px; background: var(--card); }
  .card--back  { left: 620px; top: 120px; background: var(--card-back); }

  .wordmark {
    position: absolute;
    color: var(--red);
    font-weight: 900;
    letter-spacing: 1px;
    text-transform: uppercase;
    white-space: nowrap;
  }
  .card--front .wordmark { right: 34px; top: 44px; font-size: 34px; }
  .card--back .wordmark { right: 36px; top: 120px; font-size: 34px; }
  .wordmark-dot {
    display: inline-block;
    width: 7px; height: 7px;
    background: var(--red);
    margin-left: 6px;
    vertical-align: top;
    margin-top: 6px;
  }

  .divider {
    position: absolute;
    left: 90px; right: 30px; top: 150px;
    height: 1px;
    background: var(--red);
  }
  .address {
    position: absolute;
    right: 34px; top: 160px;
    font-size: 14px;
    line-height: 1.35;
    color: var(--ink);
    text-align: left;
  }
  .person { position: absolute; left: 40px; top: 176px; }
  .person-name {
    color: var(--red);
    font-weight: 700;
    font-size: 17px;
    text-transform: uppercase;
  }
  .person-role { font-size: 15px; color: var(--ink); margin-top: 2px; }
  .person-rule {
    width: 170px; height: 1px; background: var(--red);
    margin: 9px 0 8px;
  }
  .contacts { list-style: none; font-size: 14px; line-height: 1.4; }
  .contacts li { display: flex; align-items: center; gap: 8px; }
  .contacts svg { width: 13px; height: 13px; flex: none; }
</style>
</head>
<body>

<section class="card card--front" aria-label="Business card front">
  <div class="wordmark">Ember Key Realty<span class="wordmark-dot"></span></div>
  <div class="divider"></div>
  <p class="address">18 Harbor Lane, Suite 4<br>Westfield, 20814</p>
  <div class="person">
    <p class="person-name">Daniel Marsh</p>
    <p class="person-role">Managing Director</p>
    <div class="person-rule"></div>
    <ul class="contacts">
      <li>
        <svg viewBox="0 0 24 24" aria-hidden="true"><path fill="#e00d0d" d="M6.6 10.8a15.1 15.1 0 0 0 6.6 6.6l2.2-2.2c.3-.3.7-.4 1-.2 1.1.4 2.3.6 3.6.6.6 0 1 .4 1 1V20c0 .6-.4 1-1 1A17 17 0 0 1 3 4c0-.6.4-1 1-1h3.5c.6 0 1 .4 1 1 0 1.3.2 2.5.6 3.6.1.3 0 .7-.2 1z"/></svg>
        044-987 654 321
      </li>
      <li>
        <svg viewBox="0 0 24 24" aria-hidden="true"><path fill="#e00d0d" d="M2 5h20v14H2zm2 2v.5l8 5 8-5V7z"/></svg>
        hello@emberkey.com
      </li>
      <li>
        <svg viewBox="0 0 24 24" aria-hidden="true"><g fill="none" stroke="#e00d0d" stroke-width="2"><circle cx="12" cy="12" r="9"/><path d="M3 12h18M12 3c3 3 3 15 0 18M12 3c-3 3-3 15 0 18"/></g></svg>
        www.emberkeyrealty.com
      </li>
    </ul>
  </div>
</section>

<section class="card card--back" aria-label="Business card back">
  <div class="wordmark">Ember Key Realty<span class="wordmark-dot"></span></div>
</section>

</body>
</html>
```